Website design for Puddle Jump Kidscare

I need a website designed for my daycare business, Puddle Jump Kidscare, now that I have a new logo. My former website was ok but simple and I did not have a logo yet. It also was created by me using a template and was entirely pink. I loved the bright, happy feel of it but worried it might not appeal as much to potential clients who have sons. Therefore, I need a site which will appeal to both genders while still keeping the cheerful color scheme of my new logo, which has pinks, blue, green and cream.
Updates

Reason: Hello! I am still trying to download my new logo and am sorry it is taking me so long. Hopefully I will it posted by the end of today (US Eastern Standard Time). Thank you all very much for your patience!

Hello! I have finally managed to upload my new logo for you to use in designing my website. I'm sorry it took so long and greatly appreciate your time and creative efforts! I look forward to seeing what is submitted based on my logo design and its style/colors.

Many thanks!

Reason: As I've been traveling and posted my logo file late, I am extending my deadline. I am now back and can focus on providing more and better feedback. I appreciate your patience and submissions very much!

Reason: I need more time to provide feedback and make decisions.

Industry/Entity Type

Daycare

Colors
0192cd
33a6d7
86cae7
cadf82
fbf289
add136
e34197

```html
<!DOCTYPE html>
<html lang="en">
<head>
<meta charset="utf-8">
<title>Puddle Jump Kidscare</title>
<link rel="stylesheet" href="https://fonts.googleapis.com/css2?family=Open+Sans:wght@400;600&family=Ubuntu:wght@300;400;500;700&display=swap">
<style>
  :root {
    --pink-light: #fdd3e6;
    --pink-mid: #f9b6d4;
    --berry: #b4306f;
    --berry-dark: #8e1a50;
    --heading-berry: #9e2162;
    --brown: #5b3a16;
    --brown-dark: #3f2a12;
    --green: #7fae1b;
    --green-dark: #5f8f0f;
    --news-blue: #3ea4d3;
    --text: #6a6a6a;
    --footer-bg: #f6f6f6;
    --line: #dcdcdc;
    --dot-blue: #86cae7;
  }
  * { box-sizing: border-box; margin: 0; padding: 0; }
  html, body { width: 955px; height: 1200px; overflow: hidden; background: #fff; }
  body { position: relative; font-family: "Open Sans", Arial, sans-serif; color: var(--text); }

  .site-header {
    position: absolute; left: 0; top: 0; width: 955px; height: 172px;
    background: linear-gradient(#fbc6dd, var(--pink-light) 60%, #fde0ec);
    display: flex; align-items: center; justify-content: center; gap: 10px;
  }
  .brand-mark { width: 16px; height: 16px; border-radius: 50%; background: var(--berry); }
  .brand-name { font-family: "Ubuntu", sans-serif; font-weight: 500; font-size: 30px; color: var(--berry); }

  .main-nav {
    position: absolute; left: 0; top: 172px; width: 955px; height: 47px;
    background: linear-gradient(#c03c7b, var(--berry-dark));
    display: flex; justify-content: center;
  }
  .main-nav a {
    color: #fff; text-decoration: none; font-size: 14px; line-height: 47px;
    padding: 0 19px; border-left: 1px solid rgba(255,255,255,.28);
  }
  .main-nav a:first-child { border-left: none; }

  .hero { position: absolute; left: 0; top: 219px; width: 955px; height: 391px; overflow: hidden; }
  .hero-photo {
    position: absolute; inset: 0;
    background: linear-gradient(#9ccbe6 0%, #b9d7c8 22%, #8fb04a 40%, #6f9a2a 75%, #7a8f3a 100%);
  }
  .hero-badge {
    position: absolute; left: 67px; top: 32px; width: 320px; height: 320px; border-radius: 50%;
    background: rgba(92, 66, 44, .82);
    color: #fff; text-align: center;
  }
  .hero-badge svg { position: absolute; inset: 0; }
  .hero-title { font-family: "Ubuntu", sans-serif; font-weight: 500; font-size: 37px; letter-spacing: 1px; margin-top: 106px; }
  .hero-sub { font-family: "Ubuntu", sans-serif; font-weight: 500; font-size: 18px; letter-spacing: .5px; margin-top: 2px; }
  .hero-text { font-size: 10px; line-height: 16px; margin: 12px auto 0; width: 210px; }
  .hero-dots { position: absolute; left: 443px; top: 368px; display: flex; gap: 5px; }
  .hero-dots span { width: 12px; height: 12px; border-radius: 50%; background: #fff; }

  .features {
    position: absolute; left: 58px; top: 630px; width: 837px; height: 139px;
    display: flex; border: 1px solid var(--line);
  }
  .feature {
    flex: 1; position: relative; border-left: 1px solid var(--line);
    background: linear-gradient(#fff 55%, #f6f3ee);
  }
  .feature:first-child { border-left: none; }
  .feature-art { position: absolute; left: 14px; top: 20px; width: 84px; height: 96px; border-radius: 4px; }
  .feature h3 { position: absolute; left: 106px; top: 17px; font-family: "Ubuntu", sans-serif; font-weight: 400; font-size: 20px; }
  .feature p { position: absolute; left: 106px; top: 44px; width: 165px; font-size: 10.5px; line-height: 16.5px; }
  .feature .btn {
    position: absolute; left: 106px; top: 98px; width: 86px; height: 25px; border-radius: 3px;
    color: #fff; font-size: 10px; line-height: 25px; text-align: center; text-transform: uppercase;
  }
  .learning h3 { color: var(--green); }
  .learning .btn { background: linear-gradient(#8fc43a, var(--green-dark)); }
  .learning .feature-art { background: linear-gradient(#ddd, #b9b0a8); }
  .creativity h3 { color: var(--heading-berry); }
  .creativity .btn { background: linear-gradient(#c94c86, var(--berry-dark)); }
  .creativity .feature-art { background: linear-gradient(#f2c04a, #3d8ed0); }
  .sharing h3 { color: var(--brown-dark); left: 112px; }
  .sharing p { left: 112px; top: 52px; }
  .sharing .btn { left: 112px; background: linear-gradient(#6a4a26, var(--brown-dark)); }
  .sharing .feature-art { background: linear-gradient(#e8c95a, #4a2c1a); }

  .welcome { position: absolute; left: 58px; top: 810px; width: 530px; }
  .welcome h1 { font-family: "Ubuntu", sans-serif; font-weight: 400; font-size: 27px; color: var(--heading-berry); }
  .welcome h2 { font-family: "Ubuntu", sans-serif; font-weight: 300; font-size: 19px; color: var(--brown); margin-top: 2px; }
  .welcome p { font-size: 10.5px; line-height: 18px; margin-top: 8px; }
  .welcome h2 + p { margin-top: 12px; }

  .news { position: absolute; left: 629px; top: 817px; width: 270px; }
  .news h2 { font-family: "Ubuntu", sans-serif; font-weight: 300; font-size: 24px; color: var(--green); }
  .news-item { display: flex; gap: 10px; margin-top: 12px; }
  .news-item + .news-item { margin-top: 32px; }
  .news-thumb { width: 61px; height: 61px; flex: none; }
  .news-item h3 { font-weight: 400; font-size: 12.5px; color: var(--news-blue); }
  .news-item p { font-size: 9.5px; line-height: 16.5px; }

  .site-footer { position: absolute; left: 0; top: 1091px; width: 955px; height: 109px; background: var(--footer-bg); border-top: 1px solid #e6e6e6; }
  .footer-nav { position: absolute; left: 60px; top: 27px; font-size: 12px; color: #222; }
  .footer-nav a { color: #222; text-decoration: none; }
  .footer-nav .sep { margin: 0 7px; }
  .copyright { position: absolute; left: 60px; top: 55px; font-size: 11px; color: #777; }
</style>
</head>
<body>
  <header class="site-header">
    <span class="brand-mark"></span>
    <span class="brand-name">Puddle Jump Kidscare</span>
  </header>

  <nav class="main-nav">
    <a href="#">HOME</a><a href="#">ABOUT</a><a href="#">SERVICES</a><a href="#">HOURS &amp; FEES</a><a href="#">POLICIES</a><a href="#">TESTIMONIALS</a><a href="#">PHOTOS</a><a href="#">CONTACT</a>
  </nav>

  <section class="hero">
    <div class="hero-photo" role="img" aria-label="Photo of two toddlers playing with a large ball on a grassy lawn"></div>
    <div class="hero-badge">
      <svg width="320" height="320" viewBox="0 0 320 320" aria-hidden="true">
        <circle cx="160" cy="160" r="147" fill="none" stroke="var(--dot-blue)" stroke-width="5" stroke-linecap="round" stroke-dasharray="0 9.2"/>
      </svg>
      <div class="hero-title">PLAYSCAPE</div>
      <div class="hero-sub">WHERE CHILDREN CAN PLAY</div>
      <p class="hero-text">Maecenas at justo id velit placerat molestie Donec dictum lectus non odio Cras a ante vitae enim iaculis aliquam</p>
    </div>
    <div class="hero-dots"><span></span><span></span><span></span></div>
  </section>

  <section class="features">
    <article class="feature learning">
      <div class="feature-art" role="img" aria-label="Photo of a boy sitting beside a stack of books"></div>
      <h3>LEARNING</h3>
      <p>Mauris vel lacus vitae felis ves-tibulum volutpat Etiam est nunc venenatis in tristique eu</p>
      <a class="btn">Read More</a>
    </article>
    <article class="feature creativity">
      <div class="feature-art" role="img" aria-label="Photo of children in colourful costumes"></div>
      <h3>CREATIVITY</h3>
      <p>Mauris vel lacus vitae felis ves-tibulum volutpat Etiam est nunc venenatis in tristique eu</p>
      <a class="btn">Read More</a>
    </article>
    <article class="feature sharing">
      <div class="feature-art" role="img" aria-label="Photo of a gold star trophy"></div>
      <h3>SHARING</h3>
      <p>Mauris vel lacus vitae felis ves-tibulum volutpat Etiam est nunc venenatis in tristique eu</p>
      <a class="btn">Read More</a>
    </article>
  </section>

  <section class="welcome">
    <h1>Welcome to Puddle Jump Kidscare,</h1>
    <h2>a playspace where children can play, create, and imagine!</h2>
    <p>Welcome to Puddle Jump Kidscare, a licensed Group Family Day Care, located in Maple Grove's beautiful Riverside district. We are located on a pretty, tree-lined block on Willow Lane, between Oak and Birch Avenues. We are a few blocks from the Green Line tram and the Harbor Road bus route, and we offer flexible hourly childcare, making it as easy as possible for busy parents on the go to arrange their children's care.</p>
    <p>We invite you to learn more about us and hope you will visit us soon!</p>
    <p>Etiam eu urna Sed porta Suspendisse quam leo molestie sed luctus quis feugiat in pede Fusce tellus Sed metus augue convallis et vehicula ut pulvinar eu ante Integer orci tellus tristique vitae consequat nec porta vel lectus Nulla sit amet diam Duis non nunclibero a tempus libero lectus</p>
  </section>

  <aside class="news">
    <h2>Latest News</h2>
    <div class="news-item">
      <div class="news-thumb" role="img" aria-label="Photo of children drawing at a table with a teacher" style="background:linear-gradient(135deg,#e9b48c,#4d8fc9)"></div>
      <div>
        <h3>Praesent vitae lacus</h3>
        <p>Maecenas at justo id velit placerat molestie Donec dictum lectus non odio Cras a ante vitae enim</p>
      </div>
    </div>
    <div class="news-item">
      <div class="news-thumb" role="img" aria-label="Photo of two young girls playing with blocks" style="background:linear-gradient(135deg,#f0d25a,#3fb0c8)"></div>
      <div>
        <h3>Suspendisse quam leo</h3>
        <p>Maecenas at justo id velit placerat molestie Donec dictum lectus non odio Cras a ante vitae enim</p>
      </div>
    </div>
  </aside>

  <footer class="site-footer">
    <nav class="footer-nav">
      <a href="#">HOME</a><span class="sep">|</span><a href="#">ABOUT</a><span class="sep">|</span><a href="#">SERVICES</a><span class="sep">|</span><a href="#">HOURS &amp; FEES</a><span class="sep">|</span><a href="#">POLICIES</a><span class="sep">|</span><a href="#">TESTIMONIALS</a><span class="sep">|</span><a href="#">PHOTOS</a><span class="sep">|</span><a href="#">CONTACT</a>
    </nav>
    <p class="copyright">Copyright © 2014 Company Name. All right reserved</p>
  </footer>
</body>
</html>
```